Executive recruiting firm in need of business card design

Executive recruiting firm looking for a sleek, classy and modern business card design; card itself will be square shape, rounded edges and soft touch paper, our colors are dark blues in the navy color scale, silvers and grays. Reference our website for a better idea of our company's feel and goals at Tarvex-Up.com - our company message is "Employee Engagement Begins at Recruitment" this should be on the card

```html
<!DOCTYPE html>
<html lang="en">
<head>
<meta charset="utf-8">
<title>Tarvex-Up Business Card</title>
<link rel="stylesheet" href="https://fonts.googleapis.com/css2?family=Raleway:wght@300&family=Roboto:wght@700&family=Work+Sans:wght@400&display=swap">
<style>
  :root {
    --navy: #1c1d4f;
    --navy-deep: #16173f;
    --white: #ffffff;
    --silver: #c3c5d6;
    --grey-text: #6b6b70;
    --stage: #2b2b2d;
  }
  * { margin: 0; padding: 0; box-sizing: border-box; }
  html, body { width: 1200px; height: 900px; overflow: hidden; background: var(--stage); }
  .canvas {
    width: 1200px; height: 900px;
    display: flex; align-items: center; justify-content: center; gap: 60px;
  }
  .card {
    position: relative; width: 500px; height: 500px; border-radius: 28px; overflow: hidden;
    box-shadow: 0 10px 30px rgba(0,0,0,.45);
  }
  .card--back { background: var(--navy); }
  .card--front { background: var(--white); }

  .wordmark { position: absolute; left: 44px; font-family: "Raleway", sans-serif; font-weight: 300; }
  .wordmark__name { font-size: 42px; letter-spacing: 4px; line-height: 1; white-space: nowrap; }
  .wordmark__tagline { font-size: 10px; letter-spacing: 5.4px; margin-top: 6px; padding-left: 2px; white-space: nowrap; }
  .card--back .wordmark { bottom: 112px; color: var(--white); }
  .card--front .wordmark { top: 44px; color: var(--navy); }

  .message {
    position: absolute; left: 44px; right: 44px; bottom: 48px;
    font-family: "Work Sans", sans-serif; font-size: 14px; letter-spacing: .4px;
    color: var(--silver); padding-top: 14px; border-top: 1px solid rgba(195,197,214,.35);
  }

  .emblem-circle { position: absolute; border-radius: 50%; }
  .card--back .emblem-circle { width: 230px; height: 230px; right: 40px; top: 40px; background: var(--white); }
  .card--front .emblem-circle { width: 190px; height: 190px; right: 36px; bottom: 36px; background: var(--navy-deep); }

  .contact { position: absolute; left: 44px; top: 150px; color: var(--grey-text); font-family: "Work Sans", sans-serif; }
  .contact__name { font-family: "Roboto", sans-serif; font-weight: 700; font-size: 20px; color: var(--navy); }
  .contact__role { font-size: 15px; margin-top: 2px; }
  .contact__rule { width: 16px; height: 2px; background: var(--navy); margin: 10px 0 14px; }
  .contact__list { list-style: none; font-size: 15px; line-height: 23px; }
  .contact__list li { display: flex; align-items: center; gap: 11px; }
  .contact__list svg { width: 15px; height: 15px; fill: var(--navy); flex: none; }
  .contact__address { font-size: 15px; line-height: 23px; margin-top: 12px; }
</style>
</head>
<body>
<main class="canvas">
  <section class="card card--back" aria-label="Card back">
    <div class="emblem-circle"></div>
    <div class="wordmark">
      <div class="wordmark__name">TARVEX-UP</div>
      <div class="wordmark__tagline">talent acquisition</div>
    </div>
    <p class="message">Employee Engagement Begins at Recruitment</p>
  </section>

  <section class="card card--front" aria-label="Card front">
    <div class="wordmark">
      <div class="wordmark__name">TARVEX-UP</div>
      <div class="wordmark__tagline">talent acquisition</div>
    </div>
    <div class="contact">
      <div class="contact__name">Maren Ashby</div>
      <div class="contact__role">Founder</div>
      <div class="contact__rule"></div>
      <ul class="contact__list">
        <li><svg viewBox="0 0 16 16" aria-hidden="true"><path d="M3.5 1.5l2.5 3-1.5 1.8c.9 1.9 2.3 3.3 4.2 4.2l1.8-1.5 3 2.5-1.4 2.5C7 13.6 2.4 9 1 3z"/></svg>+1.212.555.0148</li>
        <li><svg viewBox="0 0 16 16" aria-hidden="true"><path d="M4 1h8v14H4zM5.5 2.5v9h5v-9z"/></svg>917-555-0193</li>
        <li><svg viewBox="0 0 16 16" aria-hidden="true"><path d="M1 3h14v10H1zM2.5 4.5L8 9l5.5-4.5z"/></svg>mashby@tarvexup.com</li>
      </ul>
      <p class="contact__address">118 Harlow Street Suite #<br>1420 New York NY 10001</p>
    </div>
    <div class="emblem-circle"></div>
  </section>
</main>
</body>
</html>
```